Plumwick Cat Litter Logo/Package Concept

We need a logo and packaging design concept for a new brand of paper cat littler.

The product is a paper cat litter that utilises special technology to offer superior Odour and moisture absorption - making it more pleasant for customers to clean and have in their home.

It is also Biodegradable and made from Recycled Material so it is friendly to the environment and customers can feel good that they are making an ethical, responsible choice for their cat's litter.

The litter granules are also particularly appealing to cats.

Target Market(s)

Females 25-45 years, cat owners

Industry/Entity Type

Pet Care

Colors
fbed22
9bcb3b
00a990
0492cd
266eb0
6a439a

Requirements
Must have
• - A concept for the Plumwick logo
• - Product title in a large, prominent spot on the front "Paper"
• - Feel; clean, fresh, crisp, simple, inviting, anti-bacterial, sparkling, bright,
• - A close-up picture of the actual litter granules
• - A caricature of a cat OR a photo of a real cat.
• - image imposed on a 3D bag, example supplied. Can use alternative image if preferred.
Nice to have
• The ability for the design to be adapted to expand into crystal/clay littler once we introduce more products into the range.
Should not have
• anything to do with dogs
• feel to natural, holistic, earthy or dull.

```html
<!DOCTYPE html>
<html lang="en">
<head>
<meta charset="utf-8">
<title>Plumwick Cat Litter Range</title>
<link rel="stylesheet" href="https://fonts.googleapis.com/css2?family=Londrina+Solid:wght@400;900&family=Nunito:wght@700;800&display=swap">
<style>
  :root {
    --teal: #1aa892;
    --teal-deep: #12907d;
    --yellow: #fcd20a;
    --white: #ffffff;
    --ink: #2a7f72;
    --paper-orange: #f2661b;
    --clay-purple: #7b2d8a;
    --crystal-pink: #d04a82;
    --granule-light: #d9cfb8;
    --granule-dark: #9c8e72;
    --fur-light: #f1b56c;
    --fur-dark: #c87a2c;
    --gap: #ffffff;
  }
  * { box-sizing: border-box; margin: 0; padding: 0; }
  html, body { width: 1200px; height: 538px; overflow: hidden; background: var(--gap); }
  .range {
    width: 1200px; height: 538px;
    display: flex; justify-content: space-between;
  }
  .pack {
    position: relative;
    width: 393px; height: 538px;
    background: var(--teal);
    overflow: hidden;
    font-family: "Nunito", sans-serif;
  }
  .pack--paper { --accent: var(--paper-orange); }
  .pack--clay { --accent: var(--clay-purple); }
  .pack--crystal { --accent: var(--crystal-pink); }

  .brand {
    position: absolute; top: 34px; left: 0; width: 100%;
    text-align: center;
    font-family: "Londrina Solid", sans-serif;
    font-weight: 900;
    font-size: 46px; line-height: 1;
    color: var(--yellow);
    text-transform: uppercase;
    letter-spacing: 1px;
  }
  .title-row {
    position: absolute; top: 94px; left: 0; width: 100%;
    display: flex; justify-content: center;
  }
  .title {
    display: inline-block;
    padding: 2px 16px 0;
    background: var(--accent);
    border-radius: 5px 12px 7px 10px;
    transform: rotate(-1deg);
    font-family: "Londrina Solid", sans-serif;
    font-weight: 900;
    font-size: 92px; line-height: 0.98;
    color: var(--white);
    text-transform: uppercase;
    letter-spacing: 1px;
    white-space: nowrap;
  }
  .subtitle {
    position: absolute; top: 196px; left: 0; width: 100%;
    text-align: center;
    font-family: "Londrina Solid", sans-serif;
    font-weight: 900;
    font-size: 50px; line-height: 1;
    color: var(--white);
    text-transform: uppercase;
    letter-spacing: 1px;
  }
  .granules {
    position: absolute; left: 128px; top: 279px; z-index: 2;
    width: 124px; height: 124px; border-radius: 50%;
    border: 4px solid var(--yellow);
    background: radial-gradient(circle at 40% 40%, var(--granule-light), var(--granule-dark));
  }
  .icon-badge {
    position: absolute; width: 52px; height: 52px; z-index: 2;
    border-radius: 50%; border: 3px solid var(--yellow);
    background: var(--teal-deep);
    display: flex; align-items: center; justify-content: center;
  }
  .icon-badge--eco { left: 29px; top: 255px; }
  .icon-badge--odour { left: 338px; top: 290px; width: 46px; height: 46px; }
  .eco-label {
    position: absolute; left: 10px; top: 304px; z-index: 2;
    width: 94px; height: 46px;
    background: var(--white); border-radius: 8px;
    color: var(--ink); text-align: center;
    font-size: 7.5px; font-weight: 800; line-height: 1.15;
    padding-top: 6px;
  }
  .eco-label strong { display: block; font-size: 9.5px; }
  .eco-arrow { position: absolute; left: 60px; top: 348px; z-index: 1; }
  .tech-kicker {
    position: absolute; left: 259px; top: 286px;
    color: var(--white); font-size: 9.5px; font-weight: 700;
  }
  .tech-odour {
    position: absolute; left: 265px; top: 301px;
    width: 78px; height: 26px;
    background: var(--yellow); color: var(--white);
    font-size: 15px; font-weight: 800; line-height: 26px;
    padding-left: 6px;
  }
  .tech-moisture {
    position: absolute; left: 267px; top: 332px;
    width: 84px; height: 33px;
    background: var(--white); color: var(--ink);
    font-size: 10px; font-weight: 800; line-height: 1.05;
    padding: 5px 0 0 22px;
  }
  .tech-moisture::before {
    content: "+"; position: absolute; left: 6px; top: 3px;
    font-size: 18px; color: var(--ink);
  }
  .cat-photo {
    position: absolute; left: 70px; top: 362px; z-index: 1;
    width: 254px; height: 176px;
    border-radius: 46% 46% 0 0 / 30% 30% 0 0;
    background: linear-gradient(180deg, var(--fur-light), var(--fur-dark));
  }
</style>
</head>
<body>
<main class="range">

  <article class="pack pack--paper">
    <div class="brand">Plumwick</div>
    <div class="title-row"><h1 class="title">Paper</h1></div>
    <div class="subtitle">Cat Littler</div>
    <div class="icon-badge icon-badge--eco">
      <svg width="30" height="28" viewBox="0 0 30 28" fill="none" stroke="#fff" stroke-width="2" stroke-linejoin="round"><path d="M15 3 L27 24 H3 Z"/><path d="M15 11 C11 15 12 19 15 20 C18 19 19 15 15 11 Z"/></svg>
    </div>
    <div class="eco-label"><strong>Biodegradable</strong>and made from<br>Recycled Material</div>
    <svg class="eco-arrow" width="70" height="40" viewBox="0 0 70 40" fill="none" stroke="#fcd20a" stroke-width="3" stroke-linecap="round"><path d="M4 2 C6 28 30 32 60 30"/><path d="M52 23 L61 30 L52 36"/></svg>
    <div class="granules" role="img" aria-label="Close-up photo of paper litter granules"></div>
    <div class="tech-kicker">Special technology</div>
    <div class="tech-odour">+Odour</div>
    <div class="tech-moisture">moisture absorption</div>
    <div class="icon-badge icon-badge--odour">
      <svg width="26" height="24" viewBox="0 0 30 28" fill="none" stroke="#fff" stroke-width="2.2" stroke-linecap="round"><path d="M5 24 C11 18 3 12 9 4"/><path d="M13 24 C19 18 11 12 17 4"/><path d="M21 24 C27 18 19 12 25 4"/></svg>
    </div>
    <div class="cat-photo" role="img" aria-label="Photo of a ginger kitten peeking up from the bottom edge"></div>
  </article>

  <article class="pack pack--clay">
    <div class="brand">Plumwick</div>
    <div class="title-row"><h1 class="title">Clay</h1></div>
    <div class="subtitle">Cat Littler</div>
    <div class="icon-badge icon-badge--eco">
      <svg width="30" height="28" viewBox="0 0 30 28" fill="none" stroke="#fff" stroke-width="2" stroke-linejoin="round"><path d="M15 3 L27 24 H3 Z"/><path d="M15 11 C11 15 12 19 15 20 C18 19 19 15 15 11 Z"/></svg>
    </div>
    <div class="eco-label"><strong>Biodegradable</strong>and made from<br>Recycled Material</div>
    <svg class="eco-arrow" width="70" height="40" viewBox="0 0 70 40" fill="none" stroke="#fcd20a" stroke-width="3" stroke-linecap="round"><path d="M4 2 C6 28 30 32 60 30"/><path d="M52 23 L61 30 L52 36"/></svg>
    <div class="granules" role="img" aria-label="Close-up photo of clay litter granules"></div>
    <div class="tech-kicker">Special technology</div>
    <div class="tech-odour">+Odour</div>
    <div class="tech-moisture">moisture absorption</div>
    <div class="icon-badge icon-badge--odour">
      <svg width="26" height="24" viewBox="0 0 30 28" fill="none" stroke="#fff" stroke-width="2.2" stroke-linecap="round"><path d="M5 24 C11 18 3 12 9 4"/><path d="M13 24 C19 18 11 12 17 4"/><path d="M21 24 C27 18 19 12 25 4"/></svg>
    </div>
    <div class="cat-photo" role="img" aria-label="Photo of a ginger kitten peeking up from the bottom edge"></div>
  </article>

  <article class="pack pack--crystal">
    <div class="brand">Plumwick</div>
    <div class="title-row"><h1 class="title">Crystal</h1></div>
    <div class="subtitle">Cat Littler</div>
    <div class="icon-badge icon-badge--eco">
      <svg width="30" height="28" viewBox="0 0 30 28" fill="none" stroke="#fff" stroke-width="2" stroke-linejoin="round"><path d="M15 3 L27 24 H3 Z"/><path d="M15 11 C11 15 12 19 15 20 C18 19 19 15 15 11 Z"/></svg>
    </div>
    <div class="eco-label"><strong>Biodegradable</strong>and made from<br>Recycled Material</div>
    <svg class="eco-arrow" width="70" height="40" viewBox="0 0 70 40" fill="none" stroke="#fcd20a" stroke-width="3" stroke-linecap="round"><path d="M4 2 C6 28 30 32 60 30"/><path d="M52 23 L61 30 L52 36"/></svg>
    <div class="granules" role="img" aria-label="Close-up photo of crystal litter granules"></div>
    <div class="tech-kicker">Special technology</div>
    <div class="tech-odour">+Odour</div>
    <div class="tech-moisture">moisture absorption</div>
    <div class="icon-badge icon-badge--odour">
      <svg width="26" height="24" viewBox="0 0 30 28" fill="none" stroke="#fff" stroke-width="2.2" stroke-linecap="round"><path d="M5 24 C11 18 3 12 9 4"/><path d="M13 24 C19 18 11 12 17 4"/><path d="M21 24 C27 18 19 12 25 4"/></svg>
    </div>
    <div class="cat-photo" role="img" aria-label="Photo of a ginger kitten peeking up from the bottom edge"></div>
  </article>

</main>
</body>
</html>
```